Wordpress template for a mens-choire webpage

Task is to design a Wordpress template for an 98 years old estonian mens choire webpage.
Design should involve details from the attached files, choire logo and the colors of the choire flag: in horizontal orientation bright sky-blue, white, bright grass-green.
Designer signature is allowed to be added to the template, with country of origin.

Reason: Deadline extended 2 days (until 2. March 2014) to accommodate designers creativity.

Thank you everyone for your great designs!
Our project has now entered into a voting and decision phase until 14th of March 2014 (included).

```html
<!DOCTYPE html>
<html lang="en">
<head>
<meta charset="utf-8">
<title>Harjuvald Male Choir</title>
<link href="https://fonts.googleapis.com/css2?family=Arimo:wght@400;700&family=Noto+Serif:wght@400&display=swap" rel="stylesheet">
<style>
:root{
  --sky:#1e6fb0;
  --grass:#2e5e1a;
  --red:#a01414;
  --red-dark:#8e0f0f;
  --maroon:#8a1a1a;
  --blue-text:#1a6a9a;
  --cyan:#38c0ea;
  --band:#2a7aaa;
  --dark:#1d1d1d;
  --grey:#555;
  --line:#d8d8d8;
  --white:#fff;
}
*{margin:0;padding:0;box-sizing:border-box}
html,body{width:1125px;height:1200px;overflow:hidden}
body{position:relative;font-family:"Arimo",Arial,sans-serif;color:var(--grey);background:var(--white)}
.backdrop{position:absolute;inset:0}
.page{position:absolute;left:169px;top:0;width:787px;height:1200px;background:var(--white)}
.abs{position:absolute}
.topbar{left:18px;top:0;width:750px;height:19px;background:var(--red);color:var(--white);font-size:9px;display:flex;justify-content:space-between;align-items:center;padding:0 10px 0 20px}
.nav{top:51px;width:260px;height:33px;border-top:1px dotted #777;border-bottom:1px dotted #777;display:flex;justify-content:space-around;align-items:center;font-size:9px;color:var(--maroon)}
.nav-left{left:19px}.nav-right{left:506px}
.brand{left:320px;top:24px;width:148px;height:128px;display:flex;flex-direction:column;align-items:center;justify-content:center;gap:6px}
.brand-mark{width:70px;height:70px;border-radius:50%;background:var(--red)}
.brand-name{font-size:11px;font-weight:700;color:var(--red);text-align:center;line-height:1.2}
.hero{left:18px;top:114px;width:751px;height:291px;background:linear-gradient(180deg,#d9d9d9 0%,#3a4a7a 55%,#1f3a5a 100%)}
.hero-arrow{top:120px;width:22px;height:40px}
.hero-caption{left:0;bottom:0;width:100%;height:30px;background:rgba(40,40,40,.7);color:var(--white);font-size:13px;display:flex;align-items:center;padding-left:44px}
.dots{right:26px;top:11px;display:flex;gap:5px}
.dots span{width:8px;height:8px;border-radius:50%;background:var(--white)}
.dots span:first-child{background:#1e8ad0}
.card{top:424px;width:238px}
.card-photo{height:132px;border:1px solid #ccc}
.card h3{font-weight:400;font-size:13px;color:var(--blue-text);text-align:center;margin-top:10px}
.card p{font-size:8.3px;line-height:10.5px;text-align:center;margin-top:9px;padding:0 8px}
.card-rule{margin-top:15px;border-top:2px solid var(--red)}
.btn-more{display:block;width:96px;height:19px;margin:0 auto 0 66px;background:var(--red);color:var(--white);font-size:8.5px;font-weight:700;text-align:center;line-height:19px}
.divider{left:18px;top:686px;width:750px;border-top:2px solid #e0e0e0}
.heading{font-size:13px;color:var(--maroon);font-weight:400}
.video{left:18px;top:745px;width:240px;height:146px;border:1px solid #ccc;background:linear-gradient(180deg,#9a8f80,#3a2a26 60%,#1a1a1a)}
.play{left:106px;top:56px;width:28px;height:20px;border-radius:5px;background:#d32020}
.play::after{content:"";position:absolute;left:11px;top:6px;border-left:8px solid #fff;border-top:4px solid transparent;border-bottom:4px solid transparent}
.video-bar{left:0;bottom:0;width:100%;height:14px;background:#111}
.video-bar::before{content:"";position:absolute;left:4px;top:3px;width:100px;height:2px;background:#c22}
.pager{top:716px;width:20px;height:17px;border:1px solid #bbb;background:#f4f4f4;font-size:10px;color:#777;text-align:center;line-height:15px}
.testimonial{left:276px;top:752px;width:234px;height:134px;background:#f7f7f7}
.avatar{left:20px;top:8px;width:36px;height:36px;border-radius:50%;background:#8a8a8a}
.t-name{left:62px;top:12px;font-size:8.5px;font-weight:700;color:#333}
.t-role{left:62px;top:27px;font-size:7.5px;font-style:italic;color:var(--blue-text)}
.quote-mark{left:20px;top:62px;font-size:22px;color:#999;font-family:"Noto Serif",serif}
.t-text{left:50px;top:68px;width:180px;font-family:"Noto Serif",Georgia,serif;font-size:7.4px;line-height:15px;color:#666}
.search-box{left:529px;top:745px;width:240px;height:146px;border:1px solid #ddd}
.field{height:26px;border:1px solid #ccc;background:#f9f9f9;font-size:8px;color:#aaa;padding:0 10px;display:flex;align-items:center;justify-content:space-between}
.caret{width:10px;height:10px;border:1px solid #777;position:relative}
.caret::after{content:"";position:absolute;left:2px;top:3px;border-top:4px solid #333;border-left:2.5px solid transparent;border-right:2.5px solid transparent}
.lbl{font-size:8px;color:#333}
.btn-search{left:161px;top:121px;width:66px;height:20px;background:var(--sky);color:var(--white);font-size:9.5px;text-align:center;line-height:20px}
.gallery{left:18px;top:944px;width:751px;height:120px;border:1px solid #ddd}
.g-photo{top:7px;height:104px;width:202px;border:4px solid #f0f0f0;outline:1px solid #ccc}
.newsletter{left:18px;top:1078px;width:751px;height:50px;background:var(--band)}
.nl-tab{left:0;top:0;height:50px;width:190px;background:var(--cyan);clip-path:polygon(0 0,165px 0,190px 25px,165px 50px,0 50px);color:var(--white);font-size:18px;display:flex;align-items:center;padding-left:31px}
.nl-input{left:204px;top:11px;width:402px;height:28px;background:var(--white);border:1px solid #ccc;font-size:8px;color:#bbb;padding:9px 18px}
.nl-btn{left:610px;top:10px;width:130px;height:29px;background:#e03030;color:#7a0c0c;font-size:13px;text-align:center;line-height:29px}
.footer{left:18px;top:1128px;width:751px;height:72px;background:var(--dark);color:var(--white);font-size:9px}
.f-links{left:3px;top:16px}
.f-copy{left:2px;top:34px}
.social{top:16px;width:27px;height:27px;border-radius:50%;background:#e8e8e8;border:2px solid #aaa}
</style>
</head>
<body>
<svg class="backdrop" width="1125" height="1200" viewBox="0 0 1125 1200" aria-hidden="true">
  <rect width="1125" height="1200" fill="var(--grass)"/>
  <path d="M0 0H1125V560Q562 470 0 620Z" fill="#fff"/>
  <path d="M0 0H1125V210Q562 140 0 290Z" fill="var(--sky)"/>
</svg>

<div class="page">
  <div class="abs topbar"><span>Call Us : 123 456 7890</span><span>Email : info@harjuvaldchoir.com</span></div>

  <nav class="abs nav nav-left"><span>Home</span><span>About Us</span><span>Services</span></nav>
  <nav class="abs nav nav-right"><span>Events</span><span>Blog</span><span>Contact Us</span></nav>

  <section class="abs hero" role="img" aria-label="Choir members standing in blue and purple embroidered robes">
    <svg class="abs hero-arrow" style="left:20px" viewBox="0 0 22 40"><path d="M18 4L5 20L18 36" stroke="#fff" stroke-width="5" fill="none"/></svg>
    <svg class="abs hero-arrow" style="right:20px" viewBox="0 0 22 40"><path d="M4 4L17 20L4 36" stroke="#fff" stroke-width="5" fill="none"/></svg>
    <div class="abs hero-caption">98 Years of Estonian Choire
      <div class="abs dots"><span></span><span></span><span></span></div>
    </div>
  </section>

  <div class="abs brand">
    <div class="brand-mark"></div>
    <div class="brand-name">Harjuvald Male Choir</div>
  </div>

  <article class="abs card" style="left:18px">
    <div class="card-photo" role="img" aria-label="Choir on stage in front of an audience" style="background:linear-gradient(180deg,#6a5a40,#2a2a2a 60%,#8a7a6a)"></div>
    <h3>Group</h3>
    <p>Lorem ipsum dolor sit amet, consectetur adipisicing elit, sed do eiusmod tempor incididunt ut labore et dolore magna aliqua. Ut enim ad minim veniam, quis nostrud</p>
    <div class="card-rule"></div><span class="btn-more">Read More ››</span>
  </article>
  <article class="abs card" style="left:274px">
    <div class="card-photo" role="img" aria-label="Singers in red shirts performing outdoors among greenery" style="background:linear-gradient(180deg,#b8b8a8,#4a6a2a 45%,#8a2a2a)"></div>
    <h3>Church</h3>
    <p>Lorem ipsum dolor sit amet, consectetur adipisicing elit, sed do eiusmod tempor incididunt ut labore et dolore magna aliqua. Ut enim ad minim veniam, quis nostrud</p>
    <div class="card-rule"></div><span class="btn-more">Read More ››</span>
  </article>
  <article class="abs card" style="left:530px">
    <div class="card-photo" role="img" aria-label="Choir in dark blazers singing in a hall" style="background:linear-gradient(180deg,#2a2a2a,#1c2438 60%,#3a3a4a)"></div>
    <h3>Commercial</h3>
    <p>Lorem ipsum dolor sit amet, consectetur adipisicing elit, sed do eiusmod tempor incididunt ut labore et dolore magna aliqua. Ut enim ad minim veniam, quis nostrud</p>
    <div class="card-rule"></div><span class="btn-more">Read More ››</span>
  </article>

  <div class="abs divider"></div>

  <h2 class="abs heading" style="left:19px;top:716px">What We Do</h2>
  <div class="abs video" role="img" aria-label="Video of singers in dark coats before an old stone arch">
    <div class="abs play"></div><div class="abs video-bar"></div>
  </div>

  <h2 class="abs heading" style="left:274px;top:716px">Testmonials</h2>
  <div class="abs pager" style="left:470px">‹</div><div class="abs pager" style="left:494px">›</div>
  <div class="abs testimonial">
    <div class="abs avatar" role="img" aria-label="Portrait of the reviewer"></div>
    <div class="abs t-name">John Doe</div>
    <div class="abs t-role">Project Manager</div>
    <div class="abs quote-mark">“</div>
    <p class="abs t-text">Nulla ultricies ornare erat, a rutrum lacus varius nec. Pellentesque vehicula lobortis dignissim. Ut scelerisque auctor eros sed porttitor. Nullam pulvinar ultrices malesuada.</p>
  </div>

  <h2 class="abs heading" style="left:529px;top:716px">Quick Search</h2>
  <form class="abs search-box">
    <div class="abs field" style="left:10px;top:11px;width:218px">Sacramento<span class="caret"></span></div>
    <span class="abs lbl" style="left:13px;top:44px">Price Max</span>
    <span class="abs lbl" style="left:131px;top:44px">Price Min</span>
    <div class="abs field" style="left:10px;top:58px;width:97px"><span></span><span class="caret"></span></div>
    <div class="abs field" style="left:130px;top:58px;width:98px"><span></span><span class="caret"></span></div>
    <div class="abs field" style="left:10px;top:91px;width:218px">Categories<span class="caret"></span></div>
    <div class="abs btn-search">Search</div>
  </form>

  <h2 class="abs heading" style="left:21px;top:913px">Latest Gallery</h2>
  <section class="abs gallery">
    <svg class="abs" style="left:5px;top:45px" width="14" height="28" viewBox="0 0 14 28"><path d="M12 2L3 14L12 26" stroke="#888" stroke-width="2" fill="none"/></svg>
    <div class="abs g-photo" style="left:37px" role="img" aria-label="Choir members gathered indoors at a reception" style="" ><div style="width:100%;height:100%;background:linear-gradient(180deg,#8a7a5a,#1e1e22)"></div></div>
    <div class="abs g-photo" style="left:267px" role="img" aria-label="Black and white photo of the choir in a columned hall"><div style="width:100%;height:100%;background:linear-gradient(180deg,#e0e0e0,#6a6a6a)"></div></div>
    <div class="abs g-photo" style="left:503px" role="img" aria-label="Choir in black attire in front of stained glass windows"><div style="width:100%;height:100%;background:linear-gradient(180deg,#8a9aaa,#1a1a1a 60%,#7a5a3a)"></div></div>
    <svg class="abs" style="right:5px;top:45px" width="14" height="28" viewBox="0 0 14 28"><path d="M2 2L11 14L2 26" stroke="#888" stroke-width="2" fill="none"/></svg>
  </section>

  <section class="abs newsletter">
    <div class="abs nl-tab">NewsLetter</div>
    <div class="abs nl-input">Email Address</div>
    <div class="abs nl-btn">Subscribe</div>
  </section>

  <footer class="abs footer">
    <div class="abs f-links">Home &nbsp;|&nbsp; About us &nbsp;|&nbsp; Counselling &nbsp;|&nbsp; Workshop &nbsp;|&nbsp; Contact us</div>
    <div class="abs f-copy">Content copyright 2013. Estonian. All rights reserved.</div>
    <span class="abs social" style="left:654px"></span>
    <span class="abs social" style="left:688px"></span>
    <span class="abs social" style="left:721px"></span>
  </footer>
</div>
</body>
</html>
```